HearthMile business card and stationary design

We are looking for a simple yet elegant design for our mortgage company business card and stationary.

The card should include:
Name (Marcus Pell)
Title (CEO)
Phone Number (732-555-0182)
Address (48 Birchwell Court, Suite 314, Marlowe Falls, NJ 07799)
Email (email@hearthmile.example)
"NMLS" i.e. (NMLS 61947)
"Company NMLS" (Company NMLS 274615)

Contact Information for Business Card

See above

```html
<!DOCTYPE html>
<html lang="en">
<head>
<meta charset="utf-8">
<title>HearthMile Business Card</title>
<link rel="stylesheet" href="https://fonts.googleapis.com/css2?family=Montserrat:wght@400;500;600;700&display=swap">
<style>
  :root {
    --sky: #00aaee;
    --navy: #131d2a;
    --paper: #ffffff;
    --ink: #1b2330;
    --backdrop: #c9cbce;
  }
  * { box-sizing: border-box; margin: 0; padding: 0; }
  html, body { width: 1200px; height: 800px; overflow: hidden; }
  body {
    background: var(--backdrop);
    font-family: "Montserrat", sans-serif;
    position: relative;
  }
  .card {
    position: absolute;
    left: 300px;
    width: 600px;
    height: 343px;
    border-radius: 22px;
    overflow: hidden;
    box-shadow: 0 8px 22px rgba(0,0,0,0.18);
  }
  .card-front { top: 40px; background: var(--paper); }
  .card-back { top: 417px; background: var(--sky); display: flex; align-items: center; justify-content: center; }

  .brand-name {
    font-weight: 600;
    letter-spacing: 0.5px;
    color: var(--navy);
    white-space: nowrap;
  }
  .card-front .brand-name {
    position: absolute;
    left: 44px;
    top: 40px;
    font-size: 38px;
  }
  .card-back .brand-name { font-size: 62px; }

  .panel-shapes {
    position: absolute;
    inset: 0;
    width: 600px;
    height: 343px;
  }
  .holder {
    position: absolute;
    right: 30px;
    bottom: 52px;
    text-align: left;
    width: 150px;
  }
  .holder-name { color: var(--paper); font-weight: 700; font-size: 20px; white-space: nowrap; }
  .holder-title { color: var(--sky); font-weight: 500; font-size: 13px; margin-top: 4px; letter-spacing: 1px; }

  .contact-list {
    position: absolute;
    left: 44px;
    bottom: 36px;
    width: 300px;
    list-style: none;
    color: var(--ink);
    font-size: 13px;
    line-height: 1.45;
  }
  .contact-list li { display: flex; align-items: flex-start; gap: 8px; }
  .contact-list .icon { width: 12px; height: 12px; margin-top: 3px; flex: none; }
  .contact-list .licence { padding-left: 20px; margin-top: 8px; display: block; }
</style>
</head>
<body>
  <section class="card card-front" aria-label="Business card front">
    <svg class="panel-shapes" viewBox="0 0 600 343" aria-hidden="true">
      <polygon class="accent-band" points="400,0 420,0 352,343 332,343" fill="#00aaee"/>
      <polygon class="name-panel" points="436,0 600,0 600,343 368,343" fill="#131d2a"/>
    </svg>

    <div class="brand-name">HearthMile</div>

    <ul class="contact-list">
      <li>
        <svg class="icon" viewBox="0 0 12 12" aria-hidden="true"><path d="M6 0.5a4 4 0 0 1 4 4c0 3-4 7-4 7s-4-4-4-7a4 4 0 0 1 4-4z" fill="#00aaee"/><circle cx="6" cy="4.5" r="1.5" fill="#fff"/></svg>
        <span>48 Birchwell Court, Suite 314<br>Marlowe Falls, NJ 07799</span>
      </li>
      <li>
        <svg class="icon" viewBox="0 0 12 12" aria-hidden="true"><path d="M2.5 1l2 2.2-1 1.3a7 7 0 0 0 4 4l1.3-1 2.2 2-1.2 1.5C5.5 11 1 6.5 1 2.2z" fill="#00aaee"/></svg>
        <span>732-555-0182</span>
      </li>
      <li>
        <svg class="icon" viewBox="0 0 12 12" aria-hidden="true"><rect x="0.5" y="2" width="11" height="8" rx="1" fill="#00aaee"/><path d="M1 2.5l5 4 5-4" stroke="#fff" stroke-width="1" fill="none"/></svg>
        <span>info@hearthmile.example</span>
      </li>
      <li>
        <svg class="icon" viewBox="0 0 12 12" aria-hidden="true"><circle cx="6" cy="6" r="5.5" fill="#00aaee"/><path d="M0.5 6h11M6 0.5c-2.5 3-2.5 8 0 11M6 0.5c2.5 3 2.5 8 0 11" stroke="#fff" stroke-width="0.8" fill="none"/></svg>
        <span>hearthmile.example</span>
      </li>
      <li class="licence">Company NMLS 274615<br>NMLS 61947</li>
    </ul>

    <div class="holder">
      <div class="holder-name">Marcus Pell</div>
      <div class="holder-title">CEO</div>
    </div>
  </section>

  <section class="card card-back" aria-label="Business card back">
    <div class="brand-name">HearthMile</div>
  </section>
</body>
</html>
```